House Cleaning Platform for Consumers and Cleaners

UPDATE: I've attached screenshots showing a purchase flow example, something all designers have missed in their designs. PLEASE check the URLs I've included in the brief for examples of a cleaning website. I've seen mostly landing pages and nothing else.

WHAT I'M LOOKING FOR:
I need the UI designed for a house cleaning web platform from 2 separate experiences: one from the consumer end to order a cleaner to come clean their house and one from a cleaner’s end that manages their orders and manages their schedule.

The UI will need to include photo uploading for before and after photos, a checkout/cart experience w/ tips, toggle options for adding and removing rooms/extras cleaning add-ons, customer+cleaner reviews (meaning the cleaner finished the job and they can rate and review the customer as well as the customer can rate and review the cleaner), order history for consumers, job history for cleaners, profile, settings, and landing pages for both.

PLEASE DO NOT USE THE COLOR BLUE AS THE PRIMARY COLOR. Use a light green (HEX #2fdf86) instead for primary theming color.

REFERENCES:
If you'd like a few websites I've enjoyed for references, checkout:
larkpolish.example, vomby.example, and brightfernhome.example.

For sake of branding, the company name is PlumNest. Currently do not have a logo as we have not decided on the name. Logo will come later.

Feel free to reach out to me if you have any questions!
Updates

Most designer submissions were a landing page and only a landing page. Very few designed the flows I requested and none designed a schedule management page. I even updated the Brief to more clearly outline the needs and references. Only about 2-3 of the designers actually did more than a landing page. Still don't believe I received 6 designers input that I had paid for.

Target Market(s)

FULL-TIME WORKING HOUSEHOLDS, SINGLE PROFESSIONALS, SINGLE PARENTS, ELDERLY & MOBILITY CHALLENGED, BUSY BODIES.

Industry/Entity Type

Cleaning, gig work.

Number of Pages Required

5+ page

Font styles to use
Other font styles liked:
• Jost or Lexend are great Google Font options I've used in the pitch deck and horribly done app mockups.

Colors
00AB8E
00BBA5
67D7C9
C6EFE9
E9F9F6
59FF00
82FF00
B8FF75
E3FFCB
F4FFEA
FFF300
FFF600
FEFA6F
FFFEC7
FFFEE8
FFC000
F8CF3A
FAE287
FDF2CF
FEFAEE

Requirements
Must have
• Landing page, consumer flow, cleaner schedule management, checkout flow, Rate & Review for consumer and/or cleaner, order history, profile.
Nice to have
• I'd like it to be simple in design and modern, but not so simple it's boring. Iconography can sometimes break that up, but I don't want it looking busy. It's a cleaning platform so the UI should look clean.

```html
<!DOCTYPE html>
<html lang="en">
<head>
<meta charset="utf-8">
<title>PlumNest — Order Flow Screens</title>
<link href="https://fonts.googleapis.com/css2?family=Open+Sans:wght@400;600;700;800&display=swap" rel="stylesheet">
<style>
:root{
  --board:#c9c9c9;
  --ink:#111111;
  --text:#333333;
  --muted:#9a9a9a;
  --line:#e4e4e4;
  --paper:#ffffff;
  --green:#2fdf86;
  --orange:#f7931e;
  --dark:#333333;
  --card:#f3f3f3;
}
*{box-sizing:border-box;margin:0;padding:0}
html,body{width:1200px;height:563px;overflow:hidden}
body{background:var(--board);font-family:"Open Sans",sans-serif;color:var(--text);position:relative}

.screen-title{position:absolute;top:86px;width:129px;text-align:center;font-size:8.4px;font-weight:600;color:var(--ink);white-space:nowrap}
.screen{position:absolute;top:110px;width:129px;background:var(--paper);overflow:hidden}

.nav{position:absolute;top:3px;left:11px;right:11px;height:4px;display:flex;align-items:center}
.nav-brand{font-size:3.2px;font-weight:700;color:var(--green)}
.nav-links{margin-left:auto;display:flex;gap:1.6px;font-size:1.3px;color:var(--text)}
.nav-search{margin-left:2px;width:16px;height:2px;border-bottom:.2px solid var(--line);font-size:1.2px;color:var(--muted)}
.nav-login{margin-left:4px;font-size:1.3px}
.nav-signup{margin-left:1.5px;width:7px;height:2.4px;border-radius:2px;background:var(--green);font-size:1px;color:#fff;text-align:center;line-height:2.4px}

.page-title{position:absolute;top:14px;left:0;right:0;text-align:center;font-size:3.5px;font-weight:700;color:var(--ink)}
.page-rule{position:absolute;top:23px;left:0;right:0;height:.3px;background:#d9efe4}

.block{position:absolute;left:11px;right:11px}
.cols{display:grid;grid-template-columns:1fr 1fr;gap:0 7px}
.cols-3{display:grid;grid-template-columns:1fr 1fr 1fr;gap:0 3px}
.lbl{font-size:2px;font-weight:700;color:var(--ink);line-height:2.6px}
.lbl.accent{color:var(--orange);font-size:3px}
.sub{font-size:1.3px;color:var(--ink);line-height:1.8px}
.hint{font-size:1.1px;color:var(--muted);line-height:1.6px}
.hint .warn{color:var(--orange)}
.input{height:3.4px;margin-top:1.2px;border:.25px solid var(--line);border-radius:.5px;font-size:1.1px;color:#bdbdbd;padding:0 1.5px;display:flex;align-items:center;justify-content:space-between}
.input.filled{color:var(--ink)}
.input.tall{height:12px;align-items:flex-start;padding-top:1px}
.stack>.input{margin-top:2.4px}
.row-gap{height:3px}

.dot{width:1.4px;height:1.4px;border-radius:50%;border:.25px solid #c8c8c8;display:inline-block;margin-right:.8px;flex:none}
.dot.on{background:var(--green);border-color:var(--green)}
.opt{display:flex;align-items:center;font-size:1.1px;color:var(--ink)}
.radios{display:flex;gap:10px;margin-top:1.5px}

.btns{position:absolute;left:11px;display:flex;gap:4px}
.btn{width:18px;height:4.6px;border-radius:3px;font-size:1.3px;font-weight:600;display:flex;align-items:center;justify-content:center}
.btn.back{border:.25px solid var(--line);color:var(--ink);background:#fff}
.btn.next{background:var(--green);color:#fff}
.btn.small{height:2.4px;width:5px;border-radius:.4px;font-size:1px}
.btn.apply{background:var(--orange);color:#fff}
.btn.muted{background:#cfcfcf;color:#fff}

.freq{display:grid;grid-template-columns:repeat(4,1fr);gap:2.5px}
.freq-card{background:var(--card);height:29px}
.freq-card.on{background:#fff;border:.25px solid var(--green)}
.freq-head{height:6px;background:var(--dark);color:#fff;font-size:1.5px;font-weight:700;display:flex;align-items:center;justify-content:center}
.freq-card.on .freq-head{background:var(--green)}
.freq-name{margin-top:3px;font-size:1.1px;font-weight:700;color:var(--ink);text-align:center}
.freq-text{margin:.8px 2px 0;font-size:.9px;line-height:1.3px;color:#666;text-align:center}

.summary{display:flex;align-items:center;gap:3px}
.price{font-size:3px;font-weight:700;color:var(--ink)}
.bullets{margin-top:1px;font-size:.9px;line-height:1.4px;color:#555;padding-left:1px}

.pay-marks{display:flex;gap:1.5px;margin-top:3px;align-items:center}
.pay-mark{width:4px;height:2.6px;border-radius:.4px;background:#c9d3df}
.pay-mark.alt{background:#e8c27d}
.pay-mark.alt2{background:#9fb3c8}

.board-title{position:absolute;left:65px;top:295px;font-size:35px;font-weight:700;color:#000;letter-spacing:-.2px}
.board-brand{position:absolute;left:65px;top:344px;font-size:32px;font-weight:800;color:var(--green)}
</style>
</head>
<body>

<!-- Screen titles -->
<p class="screen-title" style="left:60px">Order Flow Screen 1</p>
<p class="screen-title" style="left:196px">Order Flow Screen 2</p>
<p class="screen-title" style="left:332px">Order Flow Screen 3</p>
<p class="screen-title" style="left:468px">Order Flow Screen 4</p>
<p class="screen-title" style="left:604px">Order Flow Screen 5</p>
<p class="screen-title" style="left:739px">Order Flow Screen 6</p>
<p class="screen-title" style="left:875px">Order Flow Screen 7</p>
<p class="screen-title" style="left:1011px">Order Flow Screen 8</p>

<!-- Screen 1: home size -->
<section class="screen" style="left:60px;height:103px">
  <header class="nav"><span class="nav-brand">PlumNest</span><nav class="nav-links"><span>Home</span><span>Pricing</span><span>Services</span><span>Contact</span><span>Help</span></nav><span class="nav-search">Search</span><span class="nav-login">Login</span><span class="nav-signup">Sign Up</span></header>
  <h1 class="page-title">Book Your Services Now</h1><div class="page-rule"></div>
  <div class="block cols" style="top:30px">
    <div><p class="lbl">Enter Property Zip Code</p><p class="hint">We use your zip code to match local cleaners.</p><div class="input">Zip code</div></div>
    <div><p class="lbl">Total Square Feet At Home</p><p class="hint">Enter total living area so we can size the job.</p><div class="input">Square feet</div></div>
  </div>
  <div class="block cols" style="top:48px">
    <div><p class="lbl">How Many Bedrooms?</p><p class="hint">Enter total bedrooms in the home. Offices count.</p><div class="input">Select bedrooms <span>▾</span></div></div>
    <div><p class="lbl">How Many Bathrooms?</p><p class="hint">Enter total bathrooms. Half baths count as one.</p><div class="input">Select bathrooms <span>▾</span></div></div>
  </div>
  <div class="block" style="top:67px">
    <p class="lbl">Any Pets At Home?</p><p class="hint">Pet hair adds time, so let the cleaner know ahead.</p>
    <div class="radios"><span class="opt"><i class="dot on"></i>No pets in the home</span><span class="opt"><i class="dot"></i>Dog(s)</span><span class="opt"><i class="dot"></i>Cat(s)</span><span class="opt"><i class="dot"></i>Dog(s) and Cat(s)</span></div>
  </div>
  <div class="btns" style="top:85px"><span class="btn back">Back</span><span class="btn next">Save &amp; Next</span></div>
</section>

<!-- Screen 2: exclude rooms -->
<section class="screen" style="left:196px;height:70px">
  <header class="nav"><span class="nav-brand">PlumNest</span><nav class="nav-links"><span>Home</span><span>Pricing</span><span>Services</span><span>Contact</span><span>Help</span></nav><span class="nav-search">Search</span><span class="nav-login">Login</span><span class="nav-signup">Sign Up</span></header>
  <h1 class="page-title">Book Your Services Now</h1><div class="page-rule"></div>
  <div class="block" style="top:30px">
    <p class="lbl">Do You Want To Exclude Any Bathrooms Or Bedrooms?</p>
    <p class="hint">If you don't need some rooms cleaned, exclude them here and the price will update.</p>
  </div>
  <div class="block cols" style="top:35px">
    <div class="stack"><div class="input filled"><span class="opt"><i class="dot on"></i>Exclude Bedroom(s)</span><span>−1+</span></div><div class="input filled">Do not exclude any rooms</div></div>
    <div><div class="input filled" style="margin-top:2.4px">Exclude Bathroom(s)</div></div>
  </div>
  <div class="btns" style="top:56px"><span class="btn back">Back</span><span class="btn next">Save &amp; Next</span></div>
</section>

<!-- Screen 3: condition -->
<section class="screen" style="left:332px;height:79px">
  <header class="nav"><span class="nav-brand">PlumNest</span><nav class="nav-links"><span>Home</span><span>Pricing</span><span>Services</span><span>Contact</span><span>Help</span></nav><span class="nav-search">Search</span><span class="nav-login">Login</span><span class="nav-signup">Sign Up</span></header>
  <h1 class="page-title">Book Your Services Now</h1><div class="page-rule"></div>
  <div class="block" style="top:30px">
    <p class="lbl">Condition Of Home</p>
    <p class="hint">Select the condition that is most accurate. <span class="warn">• See condition guide</span></p>
    <p class="hint">Some home conditions are not accepted. <span class="warn">• See cleaning policy</span></p>
  </div>
  <div class="block cols" style="top:37px">
    <div class="stack"><div class="input filled"><span class="opt"><i class="dot on"></i>Heavy dusty condition</span></div><div class="input filled">Good to Great condition</div></div>
    <div class="stack"><div class="input filled">Average to Good condition</div></div>
  </div>
  <div class="block" style="top:55px"><span class="opt"><i class="dot on"></i>I've read all the conditions carefully</span></div>
  <div class="btns" style="top:65px"><span class="btn back">Back</span><span class="btn next">Save &amp; Next</span></div>
</section>

<!-- Screen 4: type and add-ons -->
<section class="screen" style="left:468px;height:104px">
  <header class="nav"><span class="nav-brand">PlumNest</span><nav class="nav-links"><span>Home</span><span>Pricing</span><span>Services</span><span>Contact</span><span>Help</span></nav><span class="nav-search">Search</span><span class="nav-login">Login</span><span class="nav-signup">Sign Up</span></header>
  <h1 class="page-title">Book Your Services Now</h1><div class="page-rule"></div>
  <div class="block" style="top:30px"><p class="lbl">Type Of Cleaning</p><p class="hint">Choose the cleaning that fits your home. Please review what each one covers.</p></div>
  <div class="block cols" style="top:34px">
    <div class="input filled"><span class="opt"><i class="dot on"></i>Deep Cleaning</span><span>View details</span></div>
    <div class="input filled">Move In/Out Cleaning<span>View details</span></div>
  </div>
  <div class="block" style="top:49px"><p class="lbl">Add-On Services <span class="hint">(optional)</span></p><p class="hint">These services can be included in addition to the cleaning chosen.</p></div>
  <div class="block cols" style="top:54px">
    <div class="stack"><div class="input filled">Inside Fridge<span>›</span></div><div class="input filled">Wipe Baseboard<span>›</span></div><div class="input filled">Interior Windows<span>›</span></div></div>
    <div class="stack"><div class="input filled">Inside Cabinets<span>›</span></div><div class="input filled">Inside Oven<span>›</span></div><div class="input filled">Wet Mop Blinds<span>›</span></div></div>
  </div>
  <div class="block" style="top:76px"><span class="opt"><i class="dot on"></i>I've read all the checklists carefully</span></div>
  <div class="btns" style="top:85px"><span class="btn back">Back</span><span class="btn next">Save &amp; Next</span></div>
</section>

<!-- Screen 5: frequency -->
<section class="screen" style="left:604px;height:92px">
  <header class="nav"><span class="nav-brand">PlumNest</span><nav class="nav-links"><span>Home</span><span>Pricing</span><span>Services</span><span>Contact</span><span>Help</span></nav><span class="nav-search">Search</span><span class="nav-login">Login</span><span class="nav-signup">Sign Up</span></header>
  <h1 class="page-title">Book Your Services Now</h1><div class="page-rule"></div>
  <div class="block" style="top:30px"><p class="lbl">Frequency</p><p class="hint">How often do you want service?</p></div>
  <div class="block freq" style="top:39px">
    <div class="freq-card"><div class="freq-head">10% Discount</div><p class="freq-name">Every Two Weeks</p><p class="freq-text">A steady routine that keeps every room fresh between visits at a lower rate.</p></div>
    <div class="freq-card"><div class="freq-head">5% Discount</div><p class="freq-name">Every Four Weeks</p><p class="freq-text">A monthly reset for homes that stay tidy and need a regular deep touch.</p></div>
    <div class="freq-card on"><div class="freq-head">15% Discount</div><p class="freq-name">Weekly</p><p class="freq-text">Best value for busy homes with kids, pets and full schedules every week.</p></div>
    <div class="freq-card"><div class="freq-head">No Discount</div><p class="freq-name">One Time</p><p class="freq-text">A single visit for a move, a party or a fresh start whenever you need.</p></div>
  </div>
  <div class="btns" style="top:78px"><span class="btn back">Back</span><span class="btn next">Save &amp; Next</span></div>
</section>

<!-- Screen 6: schedule and details -->
<section class="screen" style="left:739px;height:165px">
  <header class="nav"><span class="nav-brand">PlumNest</span><nav class="nav-links"><span>Home</span><span>Pricing</span><span>Services</span><span>Contact</span><span>Help</span></nav><span class="nav-search">Search</span><span class="nav-login">Login</span><span class="nav-signup">Sign Up</span></header>
  <h1 class="page-title">Book Your Services Now</h1><div class="page-rule"></div>
  <div class="block" style="top:30px"><p class="lbl">Date Of Cleaning</p><p class="hint">Choose from available appointment times. Cleaners arrive within a 2 hour window.</p><div class="input" style="width:48%">Select date<span>▦</span></div></div>
  <div class="block" style="top:48px"><p class="lbl">Address Details</p></div>
  <div class="block cols" style="top:53px">
    <div><p class="sub">Property Address</p><div class="input">Street address</div></div>
    <div><p class="sub">Apartment Or Suite #</p><div class="input">Unit</div></div>
  </div>
  <div class="block cols-3" style="top:62px">
    <div><p class="sub">City</p><div class="input">City</div></div>
    <div><p class="sub">State</p><div class="input">State</div></div>
    <div><p class="sub">Zip Code</p><div class="input">Zip</div></div>
  </div>
  <div class="block" style="top:71px"><p class="sub">Notes Or Special Instructions?</p><div class="input tall">Gate code, parking, keys</div></div>
  <div class="block" style="top:93px"><p class="lbl">Contact Information</p></div>
  <div class="block cols" style="top:98px">
    <div><p class="sub">First Name</p><div class="input">First name</div><p class="sub" style="margin-top:2.5px">Email</p><div class="input">Email</div></div>
    <div><p class="sub">Last Name</p><div class="input">Last name</div><p class="sub" style="margin-top:2.5px">Phone</p><div class="input">Phone</div></div>
  </div>
  <div class="block" style="top:121px"><p class="lbl">Other Details</p><p class="sub">How Did You Hear About Us?</p><div class="input">Select an option<span>▾</span></div></div>
  <div class="block cols" style="top:135px">
    <div><p class="sub">Enter Coupon Code</p><div class="input filled">SAVE10<span class="btn small apply">Apply</span></div></div>
    <div><p class="sub">Enter Coupon Code</p><div class="input">Gift code<span class="btn small muted">Apply</span></div></div>
  </div>
  <div class="btns" style="top:151px"><span class="btn back">Back</span><span class="btn next">Save &amp; Next</span></div>
</section>

<!-- Screen 7: booking summary -->
<section class="screen" style="left:875px;height:418px">
  <header class="nav"><span class="nav-brand">PlumNest</span><nav class="nav-links"><span>Home</span><span>Pricing</span><span>Services</span><span>Contact</span><span>Help</span></nav><span class="nav-search">Search</span><span class="nav-login">Login</span><span class="nav-signup">Sign Up</span></header>
  <h1 class="page-title">Book Your Services Now</h1><div class="page-rule"></div>
  <div class="block" style="top:29px"><p class="lbl accent">Booking Summary</p><div class="page-rule" style="top:6px"></div></div>
  <div class="block cols" style="top:44px">
    <div><div class="summary"><span class="sub">First Clean</span><span class="price">$314.00</span></div><p class="bullets">• Deep Cleaning<br>• Inside Fridge<br>• Inside Oven</p></div>
    <div><div class="summary"><span class="sub">Recurring Cleans</span><span class="price">$126.65</span></div><p class="bullets">• Standard Cleaning<br>• Weekly<br>• 15% Discount</p></div>
  </div>
  <div class="block cols" style="top:67px">
    <div><p class="lbl">Enter Property Zip Code</p><p class="hint">We use your zip code to match local cleaners.</p><div class="input">Zip code</div></div>
    <div><p class="lbl">Total Square Feet At Home</p><p class="hint">Enter total living area to size the job.</p><div class="input">Square feet</div></div>
  </div>
  <div class="block cols" style="top:86px">
    <div><p class="lbl">How Many Bedrooms?</p><p class="hint">Enter total bedrooms in the home.</p><div class="input">Select bedrooms<span>▾</span></div></div>
    <div><p class="lbl">How Many Bathrooms?</p><p class="hint">Half baths count as one bathroom.</p><div class="input">Select bathrooms<span>▾</span></div></div>
  </div>
  <div class="block" style="top:105px"><p class="lbl">Any Pets At Home?</p><div class="radios"><span class="opt"><i class="dot on"></i>No pets in the home</span><span class="opt"><i class="dot"></i>Dog(s)</span><span class="opt"><i class="dot"></i>Cat(s)</span><span class="opt"><i class="dot"></i>Dog(s) and Cat(s)</span></div></div>
  <div class="block" style="top:123px"><p class="lbl">Do You Want To Exclude Any Bathrooms Or Bedrooms?</p></div>
  <div class="block cols" style="top:125px">
    <div class="stack"><div class="input filled"><span class="opt"><i class="dot on"></i>Exclude Bedroom(s)</span><span>−1+</span></div><div class="input filled">Do not exclude any rooms</div></div>
    <div class="stack"><div class="input filled">Exclude Bathroom(s)</div></div>
  </div>
  <div class="block" style="top:148px"><p class="lbl">Condition Of Home</p><p class="hint">Select the most accurate condition. <span class="warn">• See condition guide</span></p></div>
  <div class="block cols" style="top:152px">
    <div class="stack"><div class="input filled"><span class="opt"><i class="dot on"></i>Heavy dusty condition</span></div><div class="input filled">Good to Great condition</div></div>
    <div class="stack"><div class="input filled">Average to Good condition</div></div>
    <span class="opt" style="margin-top:2px"><i class="dot on"></i>I've read all the conditions</span>
  </div>
  <div class="block" style="top:182px"><p class="lbl">Type Of Cleaning</p></div>
  <div class="block cols" style="top:184px">
    <div class="stack"><div class="input filled"><span class="opt"><i class="dot on"></i>Deep Cleaning</span></div></div>
    <div class="stack"><div class="input filled">Move In/Out Cleaning</div></div>
  </div>
  <div class="block" style="top:200px"><p class="lbl">Add-On Services <span class="hint">(optional)</span></p></div>
  <div class="block cols" style="top:202px">
    <div class="stack"><div class="input filled">Inside Fridge</div><div class="input filled">Wipe Baseboard</div><div class="input filled">Interior Windows</div></div>
    <div class="stack"><div class="input filled">Inside Cabinets</div><div class="input filled">Inside Oven</div><div class="input filled">Wet Mop Blinds</div></div>
    <span class="opt" style="margin-top:2px"><i class="dot on"></i>I've read all the checklists</span>
  </div>
  <div class="block" style="top:237px"><p class="lbl">Frequency</p></div>
  <div class="block freq" style="top:246px">
    <div class="freq-card"><div class="freq-head">10% Discount</div><p class="freq-name">Every Two Weeks</p><p class="freq-text">A steady routine that keeps rooms fresh between visits.</p></div>
    <div class="freq-card"><div class="freq-head">5% Discount</div><p class="freq-name">Every Four Weeks</p><p class="freq-text">A monthly reset for homes that stay fairly tidy.</p></div>
    <div class="freq-card on"><div class="freq-head">15% Discount</div><p class="freq-name">Weekly</p><p class="freq-text">Best value for busy homes with full schedules.</p></div>
    <div class="freq-card"><div class="freq-head">No Discount</div><p class="freq-name">One Time</p><p class="freq-text">A single visit for a move or a fresh start.</p></div>
  </div>
  <div class="block" style="top:283px"><p class="lbl">Date Of Cleaning</p><div class="input" style="width:48%">Select date<span>▦</span></div></div>
  <div class="block" style="top:301px"><p class="lbl">Address Details</p></div>
  <div class="block cols" style="top:306px">
    <div><p class="sub">Property Address</p><div class="input">Street address</div></div>
    <div><p class="sub">Apartment Or Suite #</p><div class="input">Unit</div></div>
  </div>
  <div class="block cols-3" style="top:315px">
    <div><p class="sub">City</p><div class="input">City</div></div>
    <div><p class="sub">State</p><div class="input">State</div></div>
    <div><p class="sub">Zip Code</p><div class="input">Zip</div></div>
  </div>
  <div class="block" style="top:324px"><p class="sub">Notes Or Special Instructions?</p><div class="input tall">Gate code, parking, keys</div></div>
  <div class="block" style="top:346px"><p class="lbl">Contact Information</p></div>
  <div class="block cols" style="top:351px">
    <div><p class="sub">First Name</p><div class="input">First name</div><p class="sub" style="margin-top:2.5px">Email</p><div class="input">Email</div></div>
    <div><p class="sub">Last Name</p><div class="input">Last name</div><p class="sub" style="margin-top:2.5px">Phone</p><div class="input">Phone</div></div>
  </div>
  <div class="block" style="top:374px"><p class="lbl">Other Details</p><p class="sub">How Did You Hear About Us?</p><div class="input">Select an option<span>▾</span></div></div>
  <div class="block cols" style="top:388px">
    <div><p class="sub">Enter Coupon Code</p><div class="input filled">SAVE10<span class="btn small apply">Apply</span></div></div>
    <div><p class="sub">Enter Coupon Code</p><div class="input">Gift code<span class="btn small muted">Apply</span></div></div>
  </div>
  <div class="btns" style="top:405px"><span class="btn back">Back</span><span class="btn next">Make Payment</span></div>
</section>

<!-- Screen 8: payment -->
<section class="screen" style="left:1011px;height:74px">
  <header class="nav"><span class="nav-brand">PlumNest</span><nav class="nav-links"><span>Home</span><span>Pricing</span><span>Services</span><span>Contact</span><span>Help</span></nav><span class="nav-search">Search</span><span class="nav-login">Login</span><span class="nav-signup">Sign Up</span></header>
  <h1 class="page-title">Book Your Services Now</h1><div class="page-rule"></div>
  <div class="block" style="top:29px">
    <p class="lbl">Payment Information</p>
    <p class="hint">Your card will not be charged until the day of service.</p>
    <p class="sub">Credit Card Details</p>
    <div class="input" style="width:48%">Card number<span>MM/YY CVC</span></div>
    <div class="pay-marks" role="img" aria-label="Accepted payment cards">
      <span class="pay-mark"></span><span class="pay-mark alt2"></span><span class="pay-mark"></span><span class="pay-mark alt"></span>
      <svg width="3" height="3" viewBox="0 0 10 10" aria-hidden="true"><rect x="2" y="4.5" width="6" height="5" rx="1" fill="#e8b93a"/><path d="M3.4 4.5V3a1.6 1.6 0 0 1 3.2 0v1.5" fill="none" stroke="#e8b93a" stroke-width="1"/></svg>
      <span class="hint">Safe and secure checkout with encrypted payment.</span>
    </div>
  </div>
  <div class="btns" style="top:56px"><span class="btn next" style="width:12px;height:3.6px">Book Now</span></div>
  <p class="block hint" style="top:62px">By clicking confirm booking you are agreeing to our terms, privacy policy and booking rules.</p>
</section>

<h2 class="board-title">Order Flow Screens</h2>
<p class="board-brand">PlumNest</p>

</body>
</html>
```